Children’s entertainer/balloon artist Website Home Page and custom landing page

I need a home page design for the home page of a children and family entertainer/balloon twister’s website. I also need a custom landing page for family theatre shows performed by the same entertainer.
It will be a Wordpress website and I need the final artwork in a layer Photoshop file with all the layers clearly named and labeled.

Target Market(s)

The site visitors are mainly mums, aged between early 20’s and late 30’s. Other visitors will included companies for Christmas functions, and event organisers for corporate functions.

Industry/Entity Type

Entertainment

Number of Pages Required

2 page

Font styles to use
Sans Serif

Colors
34a6d7
f37122

Requirements
Must have
• Layout
• I have included a wireframe for the home page layout and the custom landing page for your reference. This is a guide only and I welcome your interpretation with the rough layout provided.
• This website needs to look good on all devices as it will be fully responsive.
• It needs to include a footer area on the page, that has social media and a call to action area included.
• Colours
• The main colours for the site is:
• orange (call to action colour)
• ff6800
• blue/turquoise
• 42abc3
• Pictures
• I have included images of the entertainer/balloon artist for you to use/take inspiration from.
• These images will be included on the website. I want to show lots of people having fun.
• I would like to have elements of the logo used in isolation across the website
• i.e. the octopus figure to be included in the footer or the bird element to be included in the testimonial slider etc.
• Elements to include
• Note: use the images of the entertainer in the boxes on the home page (balloon shows, balloon twisting, balloon workshops, theatre shows (the three little balloon pigs on his head)
Nice to have
Should not have
• Element to avoid
• Stock imagery of balloon sculptures - use images provided.

```html
<!DOCTYPE html>
<html lang="en">
<head>
<meta charset="utf-8">
<title>Captain Twirl – Children's Entertainer</title>
<link rel="stylesheet" href="https://fonts.googleapis.com/css2?family=Lato:wght@300;400;700;900&display=swap">
<style>
:root{
  --blue:#34a6d7;
  --orange:#f37122;
  --navy:#1b2c66;
  --navy-deep:#14214f;
  --ink:#333;
  --grey:#777;
  --black:#111;
  --white:#fff;
}
*{box-sizing:border-box;margin:0;padding:0}
html,body{width:847px;height:1200px;overflow:hidden;background:var(--white)}
body{font-family:"Lato",Arial,sans-serif;color:var(--ink);position:relative}
.abs{position:absolute}

/* Hero */
.hero{left:0;top:0;width:847px;height:453px;background:linear-gradient(90deg,var(--navy-deep) 0%,var(--navy) 40%,#2f4f9a 100%);overflow:hidden}
.hero-photo{right:0;top:0;width:560px;height:453px;background:radial-gradient(ellipse 60% 70% at 60% 50%,rgba(214,120,80,.55) 0%,rgba(70,110,190,.35) 55%,transparent 80%),linear-gradient(90deg,rgba(27,44,102,0) 0%,#3b5ba8 55%,#4a6bb5 100%)}
.brand{left:24px;top:24px;display:flex;align-items:center;gap:10px;color:var(--white);font-weight:900;font-size:24px;line-height:1}
.brand-dot{width:22px;height:22px;border-radius:50%;background:var(--orange)}
.topbar{right:28px;top:8px;display:flex;gap:22px;font-size:11px;color:var(--white);align-items:center}
.topbar span{display:flex;align-items:center;gap:6px}
.main-nav{right:28px;top:38px;display:flex;gap:22px;font-size:11px;font-weight:700;text-transform:uppercase;color:var(--white)}
.main-nav a{color:inherit;text-decoration:none;padding-bottom:6px}
.main-nav a.active{border-bottom:2px solid var(--white)}
.hero-copy{left:36px;top:262px;width:220px;font-size:15px;line-height:1.35;color:var(--white)}
.btn-outline{display:inline-block;border:1px solid var(--white);color:var(--white);font-size:10px;font-weight:700;letter-spacing:.5px;text-transform:uppercase;padding:8px 22px}
.hero-btn{left:36px;top:352px}
.slider-dots{display:flex;gap:7px}
.slider-dots i{width:8px;height:8px;border-radius:50%;background:rgba(255,255,255,.5)}
.slider-dots i.on{background:var(--white)}
.hero-dots{left:38px;top:402px}

/* Testimonial */
.avatar{left:30px;top:478px;width:54px;height:54px;border-radius:50%;background:linear-gradient(135deg,#e89a63,#b8573a);border:2px solid var(--orange)}
.avatar-name{left:22px;top:540px;font-size:8px;color:var(--grey);width:70px;text-align:center}
.quote{left:102px;top:482px;width:460px;font-size:10px;line-height:1.55;color:var(--grey)}
.contact-card{left:598px;top:490px;width:222px;height:50px;background:var(--blue);color:var(--white);display:flex;flex-direction:column;justify-content:center;padding-left:48px;text-transform:uppercase}
.contact-card .label{font-size:11px;font-weight:700;letter-spacing:.5px}
.contact-card .phone{font-size:17px;font-weight:700}
.contact-card svg{position:absolute;left:14px;top:13px}
.quote-dots{left:380px;top:558px}
.quote-dots i{background:#ccc}
.quote-dots i.on{background:var(--orange)}

/* Welcome */
.welcome{left:0;top:594px;width:847px;height:200px;background:linear-gradient(90deg,rgba(20,20,30,.92),rgba(40,45,60,.85)),linear-gradient(90deg,#6a5a4a,#4a5670)}
.section-title{font-size:17px;font-weight:700;color:var(--white);text-transform:uppercase;letter-spacing:.3px;white-space:nowrap}
.section-text{font-size:10px;line-height:1.6;color:#c9c9c9;margin-top:10px}
.welcome-col{left:28px;top:22px;width:520px}
.news-col{left:598px;top:22px;width:222px}
.btn-small{display:inline-block;margin-top:12px;border:1px solid #999;color:var(--white);font-size:9px;font-weight:700;padding:5px 12px;text-transform:uppercase}
.news-input{margin-top:10px;height:22px;background:var(--white);font-size:9px;color:#999;padding:5px 8px}

/* Services */
.tile{top:806px;width:190px;height:241px;overflow:hidden}
.tile-img{position:absolute;inset:0}
.tile-label{position:absolute;left:0;bottom:0;width:100%;height:62px;background:rgba(0,0,0,.72);color:var(--white);font-size:14px;font-weight:700;text-transform:uppercase;line-height:1.15;padding:13px 12px}
.tile-arrow{position:absolute;right:12px;bottom:20px;width:22px;height:22px;border-radius:50%;border:1px solid var(--white);display:flex;align-items:center;justify-content:center}

/* CTA */
.cta{left:28px;top:1056px;width:792px;height:60px;border:5px solid #bfe3f3;background:var(--blue);display:flex;align-items:center;padding:0 20px;color:var(--white)}
.cta-title{font-size:17px;font-weight:700;text-transform:uppercase;letter-spacing:.5px;margin-left:12px;flex:1}
.cta-phone{border:1px solid var(--white);font-size:15px;font-weight:700;padding:6px 16px;margin-right:12px}
.cta-call{border:1px solid var(--white);font-size:11px;font-weight:700;padding:8px 14px;text-transform:uppercase}

/* Footer */
.footer{left:0;top:1126px;width:847px;height:74px;background:var(--black);color:#bbb}
.footer-nav{position:absolute;left:0;top:11px;width:100%;display:flex;justify-content:center;gap:28px;font-size:9px;color:var(--white)}
.footer-rule{position:absolute;left:28px;top:33px;width:792px;height:1px;background:#333}
.copyright{position:absolute;left:28px;top:48px;font-size:8px}
.social{position:absolute;right:28px;top:45px;display:flex;gap:12px}
.social i{width:12px;height:12px;border-radius:50%;background:#bbb}
</style>
</head>
<body>

<header class="hero abs">
  <div class="hero-photo abs" role="img" aria-label="Photo of the entertainer surrounded by colourful balloon sculptures"></div>
  <div class="brand abs"><span class="brand-dot"></span>Captain Twirl</div>
  <div class="topbar abs">
    <span><svg width="12" height="9" viewBox="0 0 12 9"><rect x=".5" y=".5" width="11" height="8" fill="none" stroke="#fff"/><path d="M.5 .5 6 5l5.5-4.5" fill="none" stroke="#fff"/></svg>hello@captaintwirl.com</span>
    <span><svg width="10" height="10" viewBox="0 0 24 24"><path fill="#fff" d="M6.6 10.8a15 15 0 0 0 6.6 6.6l2.2-2.2c.3-.3.7-.4 1-.2 1.1.4 2.3.6 3.6.6.6 0 1 .4 1 1V20c0 .6-.4 1-1 1A17 17 0 0 1 3 4c0-.6.4-1 1-1h3.5c.6 0 1 .4 1 1 0 1.3.2 2.5.6 3.6.1.3 0 .7-.2 1z"/></svg>012 345 6789</span>
  </div>
  <nav class="main-nav abs">
    <a class="active">Home</a><a>Balloon Shows</a><a>Balloon Twisting</a><a>Theatre</a><a>Reviews</a><a>Contact</a>
  </nav>
  <p class="hero-copy abs">Lorem ipsum dolor sit amet, ex vim quem primis. Quot suavitate moderatius ex usu, Ridens eleifend et sea.</p>
  <span class="btn-outline hero-btn abs">Book Now</span>
  <div class="slider-dots hero-dots abs"><i class="on"></i><i></i></div>
</header>

<section class="testimonial">
  <div class="avatar abs" role="img" aria-label="Portrait of a happy parent"></div>
  <div class="avatar-name abs">Mrs. Lorem Ipsum</div>
  <p class="quote abs">Lorem ipsum dolor sit amet, ex vim quem primis. Quot suavitate moderatius ex usu, ridens eleifend et sea. Nulla facilisi tempor invidunt his, duo ea option labitur vivendo. Mei no dicta quaeque, cu quis vidit eripuit vel, at nam porro iriure sadipscing. Ex mollis denique adipisci.</p>
  <div class="contact-card abs">
    <svg width="22" height="22" viewBox="0 0 24 24"><path fill="#fff" d="M6.6 10.8a15 15 0 0 0 6.6 6.6l2.2-2.2c.3-.3.7-.4 1-.2 1.1.4 2.3.6 3.6.6.6 0 1 .4 1 1V20c0 .6-.4 1-1 1A17 17 0 0 1 3 4c0-.6.4-1 1-1h3.5c.6 0 1 .4 1 1 0 1.3.2 2.5.6 3.6.1.3 0 .7-.2 1z"/></svg>
    <span class="label">Contact the Entertainer</span>
    <span class="phone">012 345 6789</span>
  </div>
  <div class="slider-dots quote-dots abs"><i class="on"></i><i></i><i></i><i></i></div>
</section>

<section class="welcome abs" role="img" aria-label="Dimmed photo of children enjoying a balloon show">
  <div class="welcome-col abs">
    <h2 class="section-title">Welcome to Captain Twirl</h2>
    <p class="section-text">Lorem ipsum dolor sit amet, ex vim quem primis. Quot suavitate moderatius ex usu, ridens eleifend et sea. Nulla facilisi tempor invidunt his, duo ea option labitur vivendo. Mei no dicta quaeque, cu quis vidit eripuit vel, at nam porro iriure sadipscing. Ex mollis denique adipisci vim.</p>
    <span class="btn-small">Read More</span>
  </div>
  <div class="news-col abs">
    <h2 class="section-title">Sign Up for Newsletter</h2>
    <p class="section-text">Lorem ipsum dolor sit amet, ex vim quem primis. Quot suavitate moderatius ex usu.</p>
    <div class="news-input">Enter your email here</div>
    <span class="btn-small">Subscribe</span>
  </div>
</section>

<section class="services">
  <div class="tile abs" style="left:28px">
    <div class="tile-img" role="img" aria-label="Photo of a giant blue balloon at a show" style="background:linear-gradient(180deg,#d44 0%,#e9e3d8 35%,#3a8fd6 60%,#2d6fb0 100%)"></div>
    <div class="tile-label">Balloon<br>Shows</div>
    <span class="tile-arrow"><svg width="8" height="8" viewBox="0 0 8 8"><path d="M2 1l3 3-3 3" fill="none" stroke="#fff" stroke-width="1.5"/></svg></span>
  </div>
  <div class="tile abs" style="left:228px">
    <div class="tile-img" role="img" aria-label="Photo of children with twisted balloon models" style="background:linear-gradient(160deg,#8a6a5a,#c9a28a 45%,#5a4a5e)"></div>
    <div class="tile-label">Balloon<br>Twisting</div>
    <span class="tile-arrow"><svg width="8" height="8" viewBox="0 0 8 8"><path d="M2 1l3 3-3 3" fill="none" stroke="#fff" stroke-width="1.5"/></svg></span>
  </div>
  <div class="tile abs" style="left:428px">
    <div class="tile-img" role="img" aria-label="Photo of colourful balloons at a workshop" style="background:linear-gradient(160deg,#e24a7a,#f2c23a 40%,#47a8e0 70%,#6a3fa0)"></div>
    <div class="tile-label">Balloon<br>Workshops</div>
    <span class="tile-arrow"><svg width="8" height="8" viewBox="0 0 8 8"><path d="M2 1l3 3-3 3" fill="none" stroke="#fff" stroke-width="1.5"/></svg></span>
  </div>
  <div class="tile abs" style="left:628px">
    <div class="tile-img" role="img" aria-label="Photo of the entertainer on stage in a theatre show" style="background:linear-gradient(160deg,#b3121a,#e23a2a 45%,#f08a3a 70%,#8a0e14)"></div>
    <div class="tile-label">Theatre<br>Shows</div>
    <span class="tile-arrow"><svg width="8" height="8" viewBox="0 0 8 8"><path d="M2 1l3 3-3 3" fill="none" stroke="#fff" stroke-width="1.5"/></svg></span>
  </div>
</section>

<section class="cta abs">
  <svg width="22" height="22" viewBox="0 0 24 24"><path fill="#fff" d="M6.6 10.8a15 15 0 0 0 6.6 6.6l2.2-2.2c.3-.3.7-.4 1-.2 1.1.4 2.3.6 3.6.6.6 0 1 .4 1 1V20c0 .6-.4 1-1 1A17 17 0 0 1 3 4c0-.6.4-1 1-1h3.5c.6 0 1 .4 1 1 0 1.3.2 2.5.6 3.6.1.3 0 .7-.2 1z"/></svg>
  <span class="cta-title">Contact the Entertainer</span>
  <span class="cta-phone">012 345 6789</span>
  <span class="cta-call">Request a Call Back</span>
</section>

<footer class="footer abs">
  <nav class="footer-nav"><span>Home</span><span>Balloon Shows</span><span>Balloon Twisting</span><span>Theatre</span><span>Reviews</span><span>Contact</span></nav>
  <div class="footer-rule"></div>
  <p class="copyright">© 2015 – Captain Twirl | All Rights Reserved</p>
  <div class="social" aria-label="Social links"><i></i><i></i><i></i></div>
</footer>

</body>
</html>
```